Roofing Contractor business card redesign

I want to redesign my business card with a fresh, eye catching concept

Target Market(s)

Residential Roofing Clients, potential employees, and subcontractors.

Industry/Entity Type

Business

Colors

Designer to choose colors to be used in the design.

Requirements
Nice to have
• I just want something that's more pleasing to the eye. You can use a combination of either / or of my logos.

```html
<!DOCTYPE html>
<html lang="en">
<head>
<meta charset="utf-8">
<title>Steady Hands Builders – Business Card</title>
<link rel="stylesheet" href="https://fonts.googleapis.com/css2?family=Bebas+Neue&family=Ropa+Sans&display=swap">
<style>
  :root {
    --bg: #2f2f31;
    --card-white: #efefef;
    --brown: #4a1410;
    --brown-deep: #3a1c17;
    --orange: #e67025;
    --orange-light: #f4b23c;
    --text-gray: #4d4d4d;
    --rule: #bdbdbd;
    --white: #ffffff;
  }
  * { margin: 0; padding: 0; box-sizing: border-box; }
  html, body { width: 1200px; height: 960px; overflow: hidden; }
  body { background: var(--bg); position: relative; font-family: "Ropa Sans", sans-serif; }

  .card { position: absolute; width: 600px; height: 343px; overflow: hidden; }
  .card-front { left: 320px; top: 103px; background: linear-gradient(135deg, #dcdcdc 0%, var(--card-white) 35%, #f6f6f6 100%); }
  .card-back { left: 317px; top: 488px; background: linear-gradient(135deg, var(--orange-light) 0%, var(--orange) 45%, var(--orange) 100%); }

  .brand { position: absolute; left: 50px; top: 112px; width: 240px; display: flex; align-items: center; gap: 10px; }
  .brand-dot { width: 40px; height: 40px; border-radius: 50%; background: var(--orange); flex: none; }
  .brand-name { font-family: "Bebas Neue", sans-serif; color: var(--brown); font-size: 40px; line-height: 0.9; }
  .brand-name small { display: block; font-size: 22px; }

  .divider { position: absolute; left: 311px; top: 72px; width: 1px; height: 170px; background: var(--rule); }

  .contact { position: absolute; left: 339px; top: 66px; }
  .person-name { font-family: "Bebas Neue", sans-serif; font-size: 32px; color: var(--brown); line-height: 1; letter-spacing: 0.5px; }
  .person-title { color: var(--orange); font-size: 15.5px; line-height: 18px; }
  .address { margin-top: 9px; color: var(--text-gray); font-size: 15px; line-height: 18px; }
  .lines { margin-top: 7px; list-style: none; color: var(--text-gray); font-size: 15px; line-height: 19px; }
  .lines li { display: flex; align-items: center; gap: 8px; }
  .lines svg { width: 13px; height: 13px; fill: var(--brown); flex: none; }

  .band { position: absolute; left: 0; top: 288px; width: 600px; height: 30px; background: var(--orange); }
  .band-end { position: absolute; right: 0; top: 0; width: 90px; height: 30px; background: var(--brown); }
  .band-dot { position: absolute; left: 494px; top: 0; width: 30px; height: 30px; border-radius: 50%; background: var(--brown-deep); border: 2px solid var(--white); }
  .web { position: absolute; color: var(--white); font-size: 15.5px; letter-spacing: 2.6px; }
  .band .web { left: 0; width: 534px; text-align: center; top: 5px; }

  .emblem { position: absolute; left: 205px; top: 69px; width: 190px; height: 190px; border-radius: 50%; background: var(--brown-deep); border: 4px solid var(--white); display: flex; align-items: center; justify-content: center; text-align: center; }
  .emblem-name { font-family: "Bebas Neue", sans-serif; color: var(--white); font-size: 38px; line-height: 0.95; }
  .card-back .web { left: 0; width: 600px; text-align: center; top: 292px; }
</style>
</head>
<body>
  <section class="card card-front">
    <div class="brand">
      <span class="brand-dot"></span>
      <div class="brand-name">Steady Hands<small>Builders, Inc.</small></div>
    </div>
    <div class="divider"></div>
    <div class="contact">
      <h1 class="person-name">MARK DELANEY</h1>
      <p class="person-title">Ridgeline Certified Roof Inspector</p>
      <p class="person-title">Licensed Property Adjuster</p>
      <p class="address">4810 Cedar Bend Drive Suite 110<br>Oakridge, TX 75000</p>
      <ul class="lines">
        <li><svg viewBox="0 0 24 24"><path d="M6.6 10.8a15.1 15.1 0 0 0 6.6 6.6l2.2-2.2a1 1 0 0 1 1-.25 11.4 11.4 0 0 0 3.6.57 1 1 0 0 1 1 1V20a1 1 0 0 1-1 1A17 17 0 0 1 3 4a1 1 0 0 1 1-1h3.5a1 1 0 0 1 1 1c0 1.25.2 2.45.57 3.57a1 1 0 0 1-.25 1z"/></svg>(555) 210-4400</li>
        <li><svg viewBox="0 0 24 24"><path d="M7 1h10a2 2 0 0 1 2 2v18a2 2 0 0 1-2 2H7a2 2 0 0 1-2-2V3a2 2 0 0 1 2-2zm0 3v14h10V4z"/></svg>(555) 318-7720</li>
        <li><svg viewBox="0 0 24 24"><path d="M2 5h20v14H2zm2 2v.5l8 5 8-5V7l-8 5z"/></svg>mark@steadyhandstx.com</li>
      </ul>
    </div>
    <div class="band">
      <span class="web">www.steadyhandstx.com</span>
      <span class="band-end"></span>
      <span class="band-dot"></span>
    </div>
  </section>

  <section class="card card-back">
    <div class="emblem"><span class="emblem-name">Steady<br>Hands</span></div>
    <span class="web">www.steadyhandstx.com</span>
  </section>
</body>
</html>
```